Bork Ventures, Inc. Website redesign

Revamp the website, it is old and outdated. www.borkventuresinc.example

Target Market(s)

Information Technology Consulting and Staffing

Coding

Coded - Design and coding required

Number of Pages Required

5+ page

Colors

Designer to choose colors to be used in the design.

Requirements
Must have
• Outlined text boxes just like from the Tolvane.example site. A clean look

```html
<!DOCTYPE html>
<html lang="en">
<head>
<meta charset="utf-8">
<title>Bork Ventures, Inc.</title>
<link href="https://fonts.googleapis.com/css2?family=Titillium+Web:wght@400;600;700&family=Open+Sans:wght@400;600;700&family=Raleway:wght@400;500;600&display=swap" rel="stylesheet">
<style>
:root{
  --navy:#1b3468;
  --navy-deep:#13203f;
  --navy-bottom:#0f1a35;
  --red:#8b1a2e;
  --ink:#222;
  --body:#444;
  --line:#d9d9d9;
  --light:#eeeeee;
}
*{margin:0;padding:0;box-sizing:border-box}
html,body{width:1200px;height:3996px;overflow:hidden;background:#fff}
body{position:relative;font-family:"Open Sans",sans-serif;color:var(--body)}
.abs{position:absolute}
.head-font{font-family:"Titillium Web",sans-serif}

/* top bar */
.topbar{left:434px;top:0;width:766px;height:34px;background:var(--red);clip-path:polygon(0 0,100% 0,100% 100%,38px 100%)}
.topbar-info{left:505px;top:0;height:34px;display:flex;align-items:center;gap:22px;color:#fff;font-size:14px}
.topbar-info b{font-family:"Titillium Web",sans-serif;font-weight:700;font-size:16px}
.socials{display:flex;gap:5px;margin-left:6px}
.socials span{width:24px;height:24px;border:1.5px solid #fff;border-radius:50%}
.logo{left:143px;top:30px;display:flex;align-items:center;gap:10px}
.logo-name{font-family:"Titillium Web",sans-serif;font-weight:700;font-size:34px;color:var(--ink);letter-spacing:1px}
.logo-mark{width:34px;height:34px;background:var(--red)}
.nav{left:473px;top:62px;display:flex;gap:22px;font-family:"Titillium Web",sans-serif;font-weight:600;font-size:16px;color:#222}
.nav .on{color:var(--red);position:relative}
.nav .on::after{content:"";position:absolute;left:0;right:0;top:44px;height:3px;background:var(--red)}

/* hero */
.hero{left:0;top:112px;width:1200px;height:718px;background:radial-gradient(ellipse at 70% 40%,#2c4f80 0%,#12223c 55%,#070d1a 100%)}
.hero-title{left:0;width:1200px;text-align:center;color:#fff;font-family:"Titillium Web",sans-serif;font-weight:700}
.btn{display:flex;align-items:center;justify-content:center;background:var(--navy);color:#fff;font-family:"Titillium Web",sans-serif;font-weight:700;border-radius:3px}
.dots{left:558px;top:668px;display:flex;gap:8px;align-items:center}
.dots span{width:12px;height:12px;border-radius:50%;background:#fff}
.dots .cur{width:20px;height:20px;border:2px solid #fff;background:transparent;position:relative}

/* services */
.svc{width:284px;height:406px;top:732px;background:#fff;border:5px solid #fff;box-shadow:0 2px 8px rgba(0,0,0,.18);text-align:center}
.svc-photo{height:172px;width:100%}
.svc h3{margin-top:30px;font-family:"Titillium Web",sans-serif;font-weight:700;font-size:16px;color:#222}
.svc p{margin:12px 12px 0;font-size:13px;line-height:24px;color:#444;height:96px;overflow:hidden}
.svc .btn{width:118px;height:31px;margin:20px auto 0;font-size:13px}

/* welcome */
.center{left:0;width:1200px;text-align:center}
.rule{height:3px;width:62px;background:var(--navy)}
.welcome-text{left:160px;width:880px;top:1304px;text-align:center;font-size:14px;line-height:30px;color:#333}
.outline-btn{left:532px;top:1453px;width:136px;height:38px;border:2px solid var(--navy);border-radius:3px;display:flex;align-items:center;justify-content:center;font-family:"Titillium Web",sans-serif;font-weight:700;color:var(--navy);font-size:15px}

/* strategy */
.strategy{left:0;top:1588px;width:1200px;height:846px}
.strat-box{width:431px;height:210px;background:#fff;border-right:5px solid #c9d3e8;border-bottom:5px solid #c9d3e8;outline:3px solid #fff}
.strat-box h4{font-family:"Titillium Web",sans-serif;font-weight:700;font-size:18px;color:#222;margin-bottom:8px}
.strat-box p{font-size:13px;line-height:24px;color:#444}
.strat-text{position:absolute;top:30px;width:264px}
.strat-icon{position:absolute;top:36px;width:90px;height:90px;border-radius:50%;background:var(--navy);display:flex;align-items:center;justify-content:center}

/* leadership */
.lead{left:0;top:2434px;width:1200px;height:524px;background:var(--light)}
.lead-photo{left:540px;top:2434px;width:660px;height:524px;background:linear-gradient(90deg,#dcdcdc 0%,#8d8f93 45%,#2a2f38 100%)}
.lead-title{left:141px;top:2570px;z-index:2;font-family:"Titillium Web",sans-serif;font-weight:700;font-size:37px;line-height:52px;color:#333;white-space:nowrap}

/* news */
.news{left:0;top:2958px;width:1200px;height:540px;background:radial-gradient(circle at 50% 30%,#fff 0%,#f4f5f7 100%)}
.news-card{top:3159px;width:273px;height:333px;background:#fff;box-shadow:0 1px 6px rgba(0,0,0,.15)}
.news-photo{height:172px}
.news-card h5{margin:12px 14px 0;font-family:"Raleway",sans-serif;font-weight:500;font-size:18px;color:#222}
.news-date{margin:8px 14px 0;font-family:"Titillium Web",sans-serif;font-weight:700;font-size:12px;color:var(--red);display:flex;align-items:center;gap:6px}
.news-card p{margin:8px 14px 0;font-family:"Raleway",sans-serif;font-size:11px;line-height:21px;color:#333}

/* footer */
.footer{left:0;top:3495px;width:1200px;height:393px;background:var(--navy-deep)}
.foot-h{font-family:"Titillium Web",sans-serif;font-weight:700;font-size:22px;color:#fff}
.foot-list{color:#fff;font-size:13px;line-height:20px}
.contact-row{display:flex;gap:12px;align-items:flex-start;margin-bottom:14px}
.contact-row svg{flex:none;margin-top:2px}
.field{height:38px;border:1px solid #8c97b0;color:#fff;font-size:10px;padding:13px 12px}
.submit{left:670px;top:3791px;width:210px;height:38px;background:var(--red);color:#fff;font-family:"Titillium Web",sans-serif;font-weight:700;font-size:15px;display:flex;align-items:center;justify-content:center}
.bottom{left:0;top:3888px;width:1200px;height:108px;background:var(--navy-bottom);display:flex;align-items:center;justify-content:center;color:#fff;font-size:15px}
</style>
</head>
<body>

<header>
  <div class="abs topbar"></div>
  <div class="abs topbar-info">
    <span>&#9990; CALL <b>555-014-2290</b></span>
    <span>&#9993;&nbsp; info@borkventuresinc.example</span>
    <span class="socials"><span></span><span></span><span></span><span></span></span>
  </div>
  <div class="abs logo"><span class="logo-name">BORK VENTURES</span><span class="logo-mark"></span></div>
  <nav class="abs nav">
    <span class="on">HOME</span><span>ABOUT BORK VENTURES</span><span>STRATEGY</span><span>IT NEWS</span><span>BLOG</span><span>CONTACT US</span>
  </nav>
</header>

<section>
  <div class="abs hero" role="img" aria-label="Two professionals in a data center touching a glowing network display"></div>
  <h1 class="abs hero-title" style="top:368px;font-size:58px;line-height:70px">BORK VENTURES</h1>
  <div class="abs hero-title" style="top:440px;font-size:48px;line-height:64px;font-weight:600">MISSION INTEGRITY RESULTS</div>
  <div class="abs btn" style="left:515px;top:524px;width:173px;height:44px;font-size:16px">GET MORE INFO</div>
  <div class="abs dots"><span class="cur"></span><span></span><span></span><span></span></div>
</section>

<section>
  <div class="abs svc" style="left:26px">
    <div class="svc-photo" role="img" aria-label="Team gathered around a desk with monitors" style="background:linear-gradient(135deg,#9aa6b5,#4a5566)"></div>
    <h3>HARDWARE / SOFTWARE SALES</h3>
    <p>We have access to multiple distributor partners throughout North America, as well as Elite Partner Status with many of the industry's marquee</p>
    <div class="btn">LEARN MORE</div>
  </div>
  <div class="abs svc" style="left:315px">
    <div class="svc-photo" role="img" aria-label="Open plan office with staff at desks" style="background:linear-gradient(135deg,#c8cdd2,#6d747c)"></div>
    <h3>PROFESSIONAL SERVICES</h3>
    <p>Our team provides experienced leadership and guidance, utilizing the industry standard methodologies. We help you maintain a comprehensive</p>
    <div class="btn">LEARN MORE</div>
  </div>
  <div class="abs svc" style="left:603px">
    <div class="svc-photo" role="img" aria-label="Engineer with laptop in a server room" style="background:linear-gradient(135deg,#3d5d8c,#0f1f3c)"></div>
    <h3>TECHNOLOGY ASSESSMENT</h3>
    <p>Experience has shown companies that perform objective, third-party technology assessments have proven to be instrumental in identifying</p>
    <div class="btn">LEARN MORE</div>
  </div>
  <div class="abs svc" style="left:891px">
    <div class="svc-photo" role="img" aria-label="Two consultants in conversation at a table" style="background:linear-gradient(135deg,#b9c7d8,#6f8298)"></div>
    <h3>TECHNOLOGY CONSULTING</h3>
    <p>Implementing quality solutions is more than applying technology to problems. You need experts with deep technical knowledge and broad industry</p>
    <div class="btn">LEARN MORE</div>
  </div>
</section>

<section>
  <h2 class="abs center head-font" style="top:1208px;font-size:38px;font-weight:600;color:#111">Welcome to Bork Ventures</h2>
  <div class="abs rule" style="left:569px;top:1276px"></div>
  <p class="abs welcome-text">Bork Ventures, Inc. is an 8(a) innovative and rapidly growing full-service IT consulting firm. We provide our clients with cutting-edge technologies and the know-how to apply them to their individual business models. For over 20 + years, we have been providing reliable IT solutions to businesses in the Washington, DC Metro area and beyond. Our comprehensive services provide clients with unique technology solutions that are customized to meet the specific demands of their business.</p>
  <div class="abs outline-btn">READ MORE</div>
</section>

<section>
  <svg class="abs strategy" width="1200" height="846" viewBox="0 0 1200 846">
    <polygon points="0,128 600,0 1200,80 1200,846 0,846" fill="#1b3468"/>
    <polygon points="0,116 600,0 0,128" fill="#8b1a2e"/>
  </svg>
  <h2 class="abs center head-font" style="top:1686px;font-size:38px;font-weight:700;color:#fff">OUR STRATEGY</h2>
  <div class="abs center" style="top:1746px;font-size:22px;color:#fff">Your Path to Success</div>
  <div class="abs rule" style="left:569px;top:1806px;background:#fff"></div>

  <div class="abs strat-box" style="left:157px;top:1868px">
    <div class="strat-text" style="left:22px;text-align:right"><h4>MONITOR</h4><p>Ensuring that your technology performs optimally and securely at all times is our job. Bork Ventures, Inc. provides solutions that continuously monitor, assess and track the</p></div>
    <div class="strat-icon" style="left:308px"><svg width="50" height="40" viewBox="0 0 50 40" fill="none" stroke="#fff" stroke-width="2.5"><rect x="3" y="3" width="44" height="28" rx="2"/><path d="M18 37h14M25 31v6M9 24l10-9 8 6 12-12"/></svg></div>
  </div>
  <div class="abs strat-box" style="left:612px;top:1868px">
    <div class="strat-icon" style="left:28px"><svg width="50" height="50" viewBox="0 0 50 50" fill="none" stroke="#fff" stroke-width="2.5"><circle cx="23" cy="27" r="18"/><circle cx="23" cy="27" r="11"/><circle cx="23" cy="27" r="4"/><path d="M23 27l20-20M36 7h7v7"/></svg></div>
    <div class="strat-text" style="left:145px"><h4>MANAGE</h4><p>Our uniquely designed approach to systems maintenance and support helps you to reduce costs by managing your systems with greater efficiency. We provide enhanced system stability</p></div>
  </div>
  <div class="abs strat-box" style="left:157px;top:2108px">
    <div class="strat-text" style="left:22px;text-align:right"><h4>IMPLEMENT</h4><p>Bork Ventures, Inc. manages all aspects of the implementation process, including design, procurement, project management, testing, training and documentation. During the</p></div>
    <div class="strat-icon" style="left:308px"><svg width="46" height="50" viewBox="0 0 46 50" fill="none" stroke="#fff" stroke-width="2.5"><path d="M8 24a15 15 0 1 1 26 10v10H16v-6H10v-8z"/><circle cx="24" cy="20" r="5"/></svg></div>
  </div>
  <div class="abs strat-box" style="left:612px;top:2108px">
    <div class="strat-icon" style="left:28px"><svg width="48" height="48" viewBox="0 0 48 48" fill="none" stroke="#fff" stroke-width="2.5"><path d="M40 6C28 8 18 18 14 30l4 4c12-4 22-14 24-26zM14 30l-8 2 6-10M18 34l-2 8 10-6M8 40l6-6"/><circle cx="30" cy="18" r="3"/></svg></div>
    <div class="strat-text" style="left:145px"><h4>ASSESS</h4><p>Our case-specific technology audit and data gathering provides us with a detailed and comprehensive picture of your existing network architecture, IT infrastructure and working</p></div>
  </div>
</section>

<section>
  <div class="abs lead"></div>
  <div class="abs lead-photo" role="img" aria-label="Technician holding a tablet while checking a server rack"></div>
  <h2 class="abs lead-title">BRINGING THOUGHT<br>LEADERSHIP AND QUALITY<br>TO EVERY PROJECT</h2>
  <div class="abs btn" style="left:144px;top:2758px;width:180px;height:45px;font-size:17px">GET MORE INFO</div>
</section>

<section>
  <div class="abs news"></div>
  <h2 class="abs center head-font" style="top:3030px;font-size:40px;font-weight:600;color:#222">LATEST NEWS</h2>
  <div class="abs rule" style="left:563px;top:3106px;width:74px"></div>

  <article class="abs news-card" style="left:31px">
    <div class="news-photo" role="img" aria-label="Developer working at dual monitors" style="background:linear-gradient(135deg,#3c5a80,#121d30)"></div>
    <h5>Quis autem vel eum iure</h5>
    <div class="news-date"><svg width="10" height="10" viewBox="0 0 10 10"><rect x="0.5" y="1.5" width="9" height="8" fill="none" stroke="#8b1a2e"/><path d="M0.5 4h9" stroke="#8b1a2e"/></svg>OCTOBER 17, 2019</div>
    <p>Sed ut perspiciatis unde omnis iste natus error sit voluptatem accusantium doloque laium, totam rem aperiam</p>
  </article>
  <article class="abs news-card" style="left:319px">
    <div class="news-photo" role="img" aria-label="Person interacting with floating digital icons" style="background:linear-gradient(135deg,#9a9ea6,#2b2e36)"></div>
    <h5>Quis autem vel eum iure</h5>
    <div class="news-date"><svg width="10" height="10" viewBox="0 0 10 10"><rect x="0.5" y="1.5" width="9" height="8" fill="none" stroke="#8b1a2e"/><path d="M0.5 4h9" stroke="#8b1a2e"/></svg>OCTOBER 17, 2019</div>
    <p>Sed ut perspiciatis unde omnis iste natus error sit voluptatem accusantium doloque laium, totam rem aperiam</p>
  </article>
  <article class="abs news-card" style="left:608px">
    <div class="news-photo" role="img" aria-label="Technician beside server racks" style="background:linear-gradient(135deg,#5b6e86,#1c2535)"></div>
    <h5>Quis autem vel eum iure</h5>
    <div class="news-date"><svg width="10" height="10" viewBox="0 0 10 10"><rect x="0.5" y="1.5" width="9" height="8" fill="none" stroke="#8b1a2e"/><path d="M0.5 4h9" stroke="#8b1a2e"/></svg>OCTOBER 17, 2019</div>
    <p>Sed ut perspiciatis unde omnis iste natus error sit voluptatem accusantium doloque laium, totam rem aperiam</p>
  </article>
  <article class="abs news-card" style="left:896px">
    <div class="news-photo" role="img" aria-label="Busy office with rows of desks" style="background:linear-gradient(135deg,#c4c9d0,#6a7380)"></div>
    <h5>Quis autem vel eum iure</h5>
    <div class="news-date"><svg width="10" height="10" viewBox="0 0 10 10"><rect x="0.5" y="1.5" width="9" height="8" fill="none" stroke="#8b1a2e"/><path d="M0.5 4h9" stroke="#8b1a2e"/></svg>OCTOBER 17, 2019</div>
    <p>Sed ut perspiciatis unde omnis iste natus error sit voluptatem accusantium doloque laium, totam rem aperiam</p>
  </article>
</section>

<footer>
  <div class="abs footer"></div>
  <div class="abs foot-h" style="left:143px;top:3588px">CONTACT US</div>
  <div class="abs foot-h" style="left:470px;top:3588px">QUICK LINKS</div>
  <div class="abs foot-h" style="left:670px;top:3588px">REQUEST A QUOTE</div>

  <div class="abs foot-list" style="left:143px;top:3648px;width:300px">
    <div class="contact-row"><svg width="18" height="20" viewBox="0 0 18 20" fill="none" stroke="#fff" stroke-width="1.5"><path d="M9 19s7-7 7-12A7 7 0 0 0 2 7c0 5 7 12 7 12z"/><circle cx="9" cy="7" r="2.5"/></svg><span>Bork Ventures, Inc.<br>48 Larkspur Row<br>Fenwick, MD 20000</span></div>
    <div class="contact-row"><svg width="18" height="18" viewBox="0 0 18 18" fill="none" stroke="#fff" stroke-width="1.5"><path d="M4 1l3 4-2 2a10 10 0 0 0 6 6l2-2 4 3-2 3C8 17 1 10 1 3z"/></svg><span>Phone: 555-014-2290</span></div>
    <div class="contact-row"><svg width="18" height="18" viewBox="0 0 18 18" fill="#fff"><rect x="1" y="6" width="16" height="10" rx="1"/><rect x="4" y="1" width="10" height="6" fill="none" stroke="#fff" stroke-width="1.5"/></svg><span>Fax: 0330 000 1122</span></div>
    <div class="contact-row"><svg width="18" height="14" viewBox="0 0 18 14" fill="none" stroke="#fff" stroke-width="1.5"><rect x="1" y="1" width="16" height="12"/><path d="M1 1l8 7 8-7"/></svg><span>Email: info@borkventuresinc.example</span></div>
  </div>

  <div class="abs foot-list" style="left:470px;top:3648px;line-height:27.5px">Home<br>About<br>Our Services<br>Blog<br>Strategy<br>Contact us</div>

  <div class="abs foot-list" style="left:670px;top:3643px;font-size:12px">Alternatively You Can Fill In The Following Contact Form:</div>
  <div class="abs field" style="left:670px;top:3684px;width:187px">Name</div>
  <div class="abs field" style="left:866px;top:3684px;width:188px">E - Mail</div>
  <div class="abs field" style="left:670px;top:3732px;width:187px">Subject</div>
  <div class="abs field" style="left:866px;top:3732px;width:188px">Message</div>
  <div class="abs submit">SUBMIT</div>

  <div class="abs bottom">(c) 2019 Bork Ventures, Inc | All Rights Reserved | Terms and Conditions</div>
</footer>

</body>
</html>
```